Business Card Design

I give lessons and clinics for dressage riders
I would like the design to be an outline (with broad lines) of a dressage horse and rider with in background of whole card with print over top tan or parchment card with burgundy print

Industry/Entity Type

Business

Contact Information for Business Card

Dale Ferrin
612-374-2059
Classical dressage training for the modern American
Clinics, lessons, training level -Prix St. George

Requirements
Must have
• broad lined outline of dressage horse and rider

```html
<!DOCTYPE html>
<html lang="en">
<head>
<meta charset="utf-8">
<title>Dale Ferrin — Business Card</title>
<link href="https://fonts.googleapis.com/css2?family=Cinzel:wght@400&family=Arimo:wght@400&display=swap" rel="stylesheet">
<style>
  :root {
    --page-bg: #e9e6e1;
    --card-white: #ffffff;
    --panel-dark: #2b2b2b;
    --panel-mid: #555555;
    --text-light: #f2f2f2;
    --art-light: #f1f1f1;
    --art-dark: #cfcfcf;
    --card-shadow: rgba(0, 0, 0, 0.25);
  }
  html, body {
    margin: 0;
    padding: 0;
    width: 1200px;
    height: 800px;
    overflow: hidden;
    background: var(--page-bg);
  }
  .canvas {
    width: 1200px;
    height: 800px;
    display: flex;
    align-items: center;
    justify-content: center;
  }
  .business-card {
    width: 1050px;
    height: 600px;
    display: flex;
    background: var(--card-white);
    box-shadow: 0 12px 30px var(--card-shadow);
  }
  .card-art-area {
    flex: 0 0 585px;
    display: flex;
    align-items: center;
    justify-content: center;
  }
  .rider-illustration {
    width: 470px;
    height: 470px;
    border-radius: 8px;
    background: radial-gradient(ellipse at center, var(--art-dark) 0%, var(--art-light) 70%, var(--card-white) 100%);
  }
  .card-info-panel {
    flex: 1;
    background: linear-gradient(135deg, var(--panel-dark) 0%, var(--panel-mid) 100%);
    color: var(--text-light);
    display: flex;
    flex-direction: column;
    align-items: center;
    text-align: center;
    padding-top: 92px;
    box-sizing: border-box;
  }
  .holder-name {
    font-family: "Cinzel", serif;
    font-size: 44px;
    font-weight: 400;
    letter-spacing: 3px;
    margin: 0;
  }
  .holder-phone {
    font-family: "Arimo", sans-serif;
    font-size: 25px;
    letter-spacing: 1px;
    margin: 18px 0 56px;
  }
  .service-list {
    font-family: "Arimo", sans-serif;
    font-size: 24px;
    line-height: 1.25;
    margin: 0;
    padding: 0 40px;
    list-style: none;
  }
  .service-list .tagline {
    margin-bottom: 28px;
  }
</style>
</head>
<body>
  <main class="canvas">
    <section class="business-card">
      <div class="card-art-area">
        <div class="rider-illustration" role="img" aria-label="Black broad-line outline illustration of a dressage horse and rider in motion"></div>
      </div>
      <div class="card-info-panel">
        <h1 class="holder-name">Dale Ferrin</h1>
        <p class="holder-phone">612-374-2059</p>
        <ul class="service-list">
          <li class="tagline">Classical dressage training for the modern American Clinics</li>
          <li>lessons</li>
          <li>training level</li>
          <li>Prix St. George</li>
        </ul>
      </div>
    </section>
  </main>
</body>
</html>
```